Rack Card for Bright Meadow Dog Training

I love the logo you designed for me a while back (I had it updated and have the new files).

I need a rack card designed, 2 sided.

One side will be Bright Meadow Dog Training (my general dog training business)

The other side will be my Deaf and Blind Dog Training Business speciality.

Both sides Full Color/4 color

3.5 x 8.5 inches

I can provide photos and text accordingly.

Let me know the estimated price and Turn around time.

```html
<!DOCTYPE html>
<html lang="en">
<head>
<meta charset="utf-8">
<title>Bright Meadow Dog Training – Rack Card</title>
<link rel="stylesheet" href="https://fonts.googleapis.com/css2?family=Open+Sans:ital,wght@0,400;0,600;0,700;1,400&family=Kalam:wght@700&display=swap">
<style>
  :root {
    --orange: #e39a3f;
    --orange-dark: #d8862a;
    --ink: #3b3b3b;
    --charcoal: #3f3f41;
    --tan: #cfc6b4;
    --cream: #f4f1ea;
    --paper: #fbfaf7;
    --backdrop: #e6e6e4;
    --white: #ffffff;
  }
  * { box-sizing: border-box; margin: 0; padding: 0; }
  html, body { width: 1200px; height: 1083px; overflow: hidden; }
  body {
    background: var(--backdrop);
    font-family: "Open Sans", Arial, sans-serif;
    color: var(--ink);
    position: relative;
  }
  .rack-card {
    position: absolute;
    top: 42px;
    width: 412px;
    height: 1000px;
    background: var(--paper);
    overflow: hidden;
    box-shadow: 0 6px 22px rgba(0,0,0,.18);
  }
  .rack-card--general { left: 150px; }
  .rack-card--specialty { left: 638px; }
  .layer { position: absolute; left: 0; top: 0; }
  .corner-banner {
    position: absolute; left: 20px; top: 24px;
    color: var(--white); font-weight: 700; font-size: 18px; line-height: 1.3;
  }
  .brand-disc {
    position: absolute; width: 176px; height: 176px; border-radius: 50%;
    background: var(--white);
    box-shadow: 0 4px 10px rgba(0,0,0,.12);
    display: flex; align-items: center; justify-content: center; text-align: center;
  }
  .brand-name {
    font-family: "Open Sans", Arial, sans-serif;
    font-weight: 600; font-size: 21px; line-height: 1.2; color: var(--ink);
  }
  .headline {
    position: absolute; left: 178px; top: 448px; width: 226px;
    font-weight: 700; font-size: 19px; line-height: 1.3; text-align: center;
  }
  .service-list {
    position: absolute; list-style: none; font-size: 14px; line-height: 1.45;
  }
  .service-list li::before { content: "• "; }
  .photo-dot {
    position: absolute; width: 112px; height: 112px; border-radius: 50%;
    border: 4px solid var(--tan);
    box-shadow: 0 4px 8px rgba(0,0,0,.15);
  }
  .script-line {
    position: absolute; left: 0; width: 100%; text-align: center;
    font-family: "Kalam", cursive; font-weight: 700; color: var(--ink);
  }
  .url-pill {
    position: absolute; height: 34px; border-radius: 17px;
    background: var(--orange); color: var(--white);
    font-weight: 700; font-size: 16px; line-height: 34px;
    padding-left: 52px; padding-right: 16px;
  }
  .globe {
    position: absolute; left: -4px; top: -5px; width: 44px; height: 44px;
    border-radius: 50%; background: var(--charcoal); border: 3px solid var(--cream);
    display: flex; align-items: center; justify-content: center;
  }
  .contact-lines {
    position: absolute; left: 0; width: 100%; text-align: center;
    color: var(--white); font-size: 15px; line-height: 1.5; letter-spacing: .2px;
  }
  .section-title {
    position: absolute; left: 0; width: 100%; top: 452px; text-align: center;
    font-weight: 700; font-size: 20px;
  }
  .detail-copy {
    position: absolute; left: 30px; width: 360px; font-size: 13px; line-height: 1.35;
  }
  .fine-print { font-size: 9.5px; font-style: italic; }
  .package-box {
    position: absolute; left: 26px; top: 712px; width: 362px; height: 120px;
    border: 2px solid var(--orange); border-radius: 8px; background: var(--cream);
  }
  .package-header {
    position: absolute; left: 48px; top: -14px; width: 266px; height: 30px; border-radius: 15px;
    background: var(--charcoal); color: var(--white); text-align: center;
    font-weight: 700; font-size: 13px; line-height: 30px; letter-spacing: .3px;
  }
  .package {
    position: absolute; top: 26px; width: 160px; font-size: 13px; line-height: 1.3;
  }
  .package h3 { color: var(--orange-dark); font-size: 13px; font-weight: 700; }
  .package-divider { position: absolute; left: 180px; top: 28px; width: 1px; height: 58px; background: var(--ink); }
  .package-note { position: absolute; left: 0; width: 100%; bottom: 8px; text-align: center; font-size: 9.5px; font-style: italic; }
</style>
</head>
<body>

<!-- General training side -->
<section class="rack-card rack-card--general">
  <svg class="layer" width="412" height="1000" viewBox="0 0 412 1000" aria-hidden="true">
    <path d="M0 500 Q180 410 412 290 L412 1000 L0 1000 Z" fill="var(--tan)"/>
    <path d="M0 512 Q190 430 412 306 L412 1000 L0 1000 Z" fill="var(--paper)"/>
    <path d="M0 840 Q200 790 412 830 L412 1000 L0 1000 Z" fill="var(--cream)"/>
    <path d="M0 878 Q200 840 412 852 L412 1000 L0 1000 Z" fill="var(--charcoal)"/>
  </svg>
  <svg class="layer" width="412" height="500" viewBox="0 0 412 500" role="img" aria-label="Photo: trainer giving a high five to a white puppy on a grassy lawn">
    <defs>
      <linearGradient id="meadowA" x1="0" y1="0" x2="0" y2="1">
        <stop offset="0" stop-color="#5f7a3a"/>
        <stop offset=".55" stop-color="#86a356"/>
        <stop offset="1" stop-color="#a4bb6e"/>
      </linearGradient>
    </defs>
    <path d="M0 0 H412 V290 Q180 410 0 500 Z" fill="url(#meadowA)"/>
  </svg>
  <svg class="layer" width="290" height="130" viewBox="0 0 290 130" aria-hidden="true">
    <path d="M0 0 H270 Q240 95 120 108 Q50 114 0 118 Z" fill="var(--orange)"/>
  </svg>
  <p class="corner-banner">Dog Training &amp;<br>Behavioral Services</p>

  <div class="brand-disc" style="left:-6px; top:370px;">
    <span class="brand-name">Bright<br>Meadow</span>
  </div>

  <h1 class="headline">Having a happy, well-balanced dog is one of life’s greatest pleasures!</h1>

  <ul class="service-list" style="left:30px; top:570px;">
    <li>Puppy Training</li><li>House Breaking</li><li>Leash Training</li><li>Obedience</li>
  </ul>
  <ul class="service-list" style="left:212px; top:556px;">
    <li>Rescue Dog Training</li><li>Separation Anxiety</li><li>Socialization</li><li>And much more...</li>
  </ul>

  <div class="photo-dot" role="img" aria-label="Photo: happy mixed-breed dog" style="left:28px; top:660px; background:radial-gradient(circle,#8a6a4a,#4f3f30);"></div>
  <div class="photo-dot" role="img" aria-label="Photo: tilted-head vizsla" style="left:148px; top:650px; background:radial-gradient(circle,#b0703a,#3a2a20);"></div>
  <div class="photo-dot" role="img" aria-label="Photo: small dog among torn stuffing" style="left:268px; top:642px; background:radial-gradient(circle,#9a5a30,#dcd8d0);"></div>

  <p class="script-line" style="top:794px; font-size:16px;">Schedule Free 15 Minute Phone Consultation</p>

  <div class="url-pill" style="left:52px; top:842px;">
    <span class="globe"><svg width="24" height="24" viewBox="0 0 24 24" fill="none" stroke="#fff" stroke-width="1.6"><circle cx="12" cy="12" r="10"/><ellipse cx="12" cy="12" rx="4.5" ry="10"/><path d="M2 12h20M4 7h16M4 17h16"/></svg></span>
    brightmeadowdogtraining.com
  </div>

  <p class="contact-lines" style="top:914px;">LOS ANGELES (310) 555-0148<br>ORANGE COUNTY (714) 555-0162</p>
</section>

<!-- Deaf and blind specialty side -->
<section class="rack-card rack-card--specialty">
  <svg class="layer" width="412" height="1000" viewBox="0 0 412 1000" aria-hidden="true">
    <path d="M0 440 Q200 450 412 360 L412 1000 L0 1000 Z" fill="var(--tan)"/>
    <path d="M0 452 Q200 464 412 376 L412 1000 L0 1000 Z" fill="var(--paper)"/>
    <path d="M0 870 Q200 870 412 900 L412 1000 L0 1000 Z" fill="var(--cream)"/>
    <path d="M0 906 Q200 900 412 930 L412 1000 L0 1000 Z" fill="var(--charcoal)"/>
  </svg>
  <svg class="layer" width="412" height="440" viewBox="0 0 412 440" role="img" aria-label="Photo: German shepherd lying in the grass">
    <defs>
      <linearGradient id="meadowB" x1="0" y1="0" x2="0" y2="1">
        <stop offset="0" stop-color="#9aa65a"/>
        <stop offset=".5" stop-color="#6f8a3c"/>
        <stop offset="1" stop-color="#4e6a2c"/>
      </linearGradient>
    </defs>
    <path d="M0 0 H412 V360 Q200 450 0 440 Z" fill="url(#meadowB)"/>
  </svg>
  <svg class="layer" width="290" height="130" viewBox="0 0 290 130" aria-hidden="true">
    <path d="M0 0 H270 Q240 95 120 108 Q50 114 0 118 Z" fill="var(--orange)"/>
  </svg>
  <p class="corner-banner">Deaf and Blind<br>Dog Training</p>

  <div class="brand-disc" style="left:-6px; top:292px;">
    <span class="brand-name">Bright<br>Meadow</span>
  </div>

  <h2 class="section-title">Private Lessons For:</h2>
  <ul class="service-list" style="left:40px; top:488px; font-size:17px;">
    <li>Adult Dogs</li><li>Puppies</li>
  </ul>
  <ul class="service-list" style="left:230px; top:500px; font-size:17px;">
    <li>Deaf Dogs</li><li>Blind Dogs</li>
  </ul>

  <p class="detail-copy" style="top:562px;">We come to your home or mutually agreed upon location (parks, shopping malls, etc)</p>
  <ul class="service-list detail-copy" style="top:604px; font-size:13px; line-height:1.35;">
    <li>Initial Training Evaluation: $250</li>
    <li>Individual Private Lessons last 75-90 minutes: $210 per lesson</li>
  </ul>
  <p class="detail-copy fine-print" style="top:674px;">Additional nominal fees for travel outside our normal service area</p>

  <div class="package-box">
    <div class="package-header">PRIVATE LESSON PACKAGES</div>
    <div class="package" style="left:14px;">
      <h3>STARTER PACKAGE</h3>
      <p>(4) Prepaid Private Lessons $800</p>
    </div>
    <div class="package-divider"></div>
    <div class="package" style="left:196px;">
      <h3>CLASSIC PACKAGE</h3>
      <p>(8) Prepaid Private Lessons $1470</p>
    </div>
    <p class="package-note">(Buy 7 Prepaid Private Lessons and Your 8th Lesson is FREE)</p>
  </div>

  <p class="script-line" style="top:840px; font-size:15px; line-height:1.25;">NOW AVAILABLE!<br>Virtual Private Dog Training MeetLink – CallView</p>

  <div class="url-pill" style="left:52px; top:892px;">
    <span class="globe"><svg width="24" height="24" viewBox="0 0 24 24" fill="none" stroke="#fff" stroke-width="1.6"><circle cx="12" cy="12" r="10"/><ellipse cx="12" cy="12" rx="4.5" ry="10"/><path d="M2 12h20M4 7h16M4 17h16"/></svg></span>
    brightmeadowdogtraining.com
  </div>

  <p class="contact-lines" style="top:942px; font-size:14px; line-height:1.4;">LOS ANGELES (310) 555-0148<br>ORANGE COUNTY (714) 555-0162</p>
</section>

</body>
</html>
```